Psychiatric Office Needs a Website- 1st Time Ever!

Been in practice since 2003 with no website, but finally ready to dive in. We are Maplecrest Behavioral Healthcare, a mental health outpatient practice based in Fayetteville, Georgia that sees diverse individuals and families from childhood to advanced age for a variety of conditions. We've grown by word of mouth and referral but would now like to have a digital footprint. Be the pioneer of our website and we will be sure to share. We would like to see designs that are modern, animated, fairly colorful, easy to read, and caters to all ages. Also, we would like the design to take the whole page (not be centered) and can be viewed well on phone/tablet. Please see our outline for more information. Our motto/slogan is: Maplecrest Behavioral Healthcare- A step forward in your wellness journey, so the design should try to reflect that.
Updates

Project Deadline Extended
Reason: site in progress

Target Market(s)

Children through elderly

Industry/Entity Type

Medical

Logo Text

Stepping forward in your wellness journey

Number of Pages Required

1 page

Colors

Designer to choose colors to be used in the design.

Requirements
Must have
• Animation or moving pictures.
• Color.
• Concise.
• User friendly
• Diversity in the stock photos

```html
<!DOCTYPE html>
<html lang="en">
<head>
<meta charset="utf-8">
<title>Maplecrest Behavioral Healthcare</title>
<link href="https://fonts.googleapis.com/css2?family=Oswald:wght@400;500;600&family=Open+Sans:wght@400;600;700&display=swap" rel="stylesheet">
<style>
:root{
  --blue:#0b7fd4;
  --blue-dark:#0a66ad;
  --green:#6cbf2c;
  --green-dark:#4d9a1a;
  --ink:#1e1e1e;
  --text:#666;
  --muted:#999;
  --dark:#1d1d1d;
  --footer-text:#cfcfcf;
  --line:#e3e3e3;
}
*{box-sizing:border-box;margin:0;padding:0}
html,body{width:1200px;height:3666px;overflow:hidden}
body{position:relative;background:#fff;font-family:"Open Sans",Arial,sans-serif;color:var(--text)}
.abs{position:absolute}
.heading{font-family:"Oswald",Arial,sans-serif;font-weight:500;color:var(--ink);text-transform:uppercase;text-align:center;font-size:34px;letter-spacing:.5px}

/* top bar & header */
.topbar{left:538px;top:0;width:662px;height:32px;background:var(--blue);clip-path:polygon(22px 0,100% 0,100% 100%,0 100%);color:#fff;font-size:13px;font-weight:600;display:flex;align-items:center;gap:26px;padding-left:52px}
.topbar span.sep{opacity:.7}
.nav{top:66px;left:0;width:1200px;height:30px}
.nav a{position:absolute;font-size:13px;color:#333;text-decoration:none;text-transform:uppercase;font-weight:600;font-family:"Oswald",Arial,sans-serif;font-weight:400;letter-spacing:.3px}
.logo{left:98px;top:-20px;width:210px;height:210px;border-radius:50%;background:#fff;z-index:5;display:flex;flex-direction:column;align-items:center;justify-content:center;text-align:center;box-shadow:0 4px 10px rgba(0,0,0,.08)}
.logo .name{font-family:"Oswald",Arial,sans-serif;color:var(--blue);font-size:19px;line-height:1.2;width:160px;margin-top:10px}
.logo .tag{font-size:11px;color:#555;margin-top:10px}
.logo .dot{width:56px;height:56px;border-radius:50%;background:var(--green)}

/* hero */
.hero{left:0;top:118px;width:1200px;height:640px;background:linear-gradient(100deg,#dfe3e6 0%,#cfd6dc 30%,#b98a67 60%,#1f8fc0 85%,#d5dde3 100%)}
.hero-title{left:98px;top:380px;color:#fff;font-family:"Oswald",Arial,sans-serif;font-size:37px;line-height:54px;text-transform:uppercase;letter-spacing:.5px;text-shadow:0 1px 4px rgba(0,0,0,.35)}
.btn-outline{left:98px;top:537px;width:180px;height:44px;border:1.5px solid #fff;border-radius:22px;color:#fff;font-size:13px;font-weight:700;text-transform:uppercase;display:flex;align-items:center;justify-content:center;letter-spacing:.5px}
.arrow{width:36px;height:36px;border-radius:50%;background:rgba(0,0,0,.45);display:flex;align-items:center;justify-content:center}
.wave{left:0;width:1200px}

/* services */
.intro{left:280px;top:905px;width:640px;text-align:center;font-size:12px;line-height:22px;color:var(--text)}
.service{top:990px;width:225px;height:200px;text-align:center}
.service .card{position:absolute;left:0;top:50px;width:225px;height:140px;border-radius:0 0 112px 112px;box-shadow:0 6px 8px rgba(0,0,0,.12);background:#fff}
.service .icon{position:absolute;left:62px;top:0;width:100px;height:100px;border-radius:50%;background:linear-gradient(180deg,var(--green) 0%,var(--green) 45%,var(--blue) 55%,var(--blue) 100%);border:4px solid #fff;box-shadow:0 2px 6px rgba(0,0,0,.18);display:flex;align-items:center;justify-content:center}
.service .label{position:absolute;left:0;top:118px;width:225px;font-size:13px;line-height:20px;text-transform:uppercase;color:#333}

/* about */
.about-panel{left:0;top:1278px;width:620px;height:416px;background:var(--blue);color:#fff}
.about-panel h2{position:absolute;left:98px;top:64px;font-family:"Oswald",Arial,sans-serif;font-weight:500;font-size:34px;text-transform:uppercase}
.about-panel p{position:absolute;left:98px;width:470px;font-size:12.5px;line-height:22px}
.about-photo{left:620px;top:1278px;width:580px;height:416px;background:linear-gradient(135deg,#4f7a3a 0%,#7aa25a 40%,#2d8bd0 70%,#e9e9e9 100%)}
.btn-white{left:98px;top:1586px;width:140px;height:38px;border:1.5px solid #fff;border-radius:19px;color:#fff;font-size:12px;font-weight:700;display:flex;align-items:center;justify-content:center;text-transform:uppercase}

/* blogs */
.post{top:1882px;width:270px}
.post .thumb{width:270px;height:158px;border:4px solid #eee}
.post h3{margin-top:36px;font-family:"Oswald",Arial,sans-serif;font-weight:500;font-size:17px;color:#222;text-transform:uppercase}
.meta{font-size:11.5px;color:var(--muted);margin-top:8px;display:flex;align-items:center;gap:6px}
.meta i{display:inline-block;width:10px;height:10px;background:var(--green);border-radius:2px}
.post p{margin-top:12px;font-size:12px;line-height:19px;color:var(--text)}
.news{left:740px;width:400px;height:90px}
.news .thumb{position:absolute;left:0;top:0;width:95px;height:80px;border:3px solid #eee}
.news h4{position:absolute;left:118px;top:0;width:270px;font-family:"Oswald",Arial,sans-serif;font-weight:400;font-size:17px;line-height:26px;color:#222;text-transform:uppercase}
.news .meta{position:absolute;left:118px;top:58px;margin:0}

/* testimonials */
.testimonials{left:0;top:2273px;width:1200px;height:457px;background:linear-gradient(135deg,#3a2e26 0%,#5a4638 50%,#3d3029 100%)}
.testimonials .heading{color:#fff;position:absolute;left:0;top:70px;width:1200px}
.avatar{left:538px;top:2416px;width:124px;height:124px;border-radius:50%;background:linear-gradient(160deg,#c59a7e,#7d4b3a);border:5px solid #fff}
.quote{left:300px;top:2555px;width:600px;text-align:center;color:#fff;font-size:12px;font-weight:700;line-height:22px}
.qmark{font-family:Georgia,serif;color:#fff;font-size:60px;line-height:1}
.author{left:0;top:2628px;width:1200px;text-align:center;color:#fff;font-size:14px;font-weight:700}
.author span{font-weight:400}

/* faq */
.faq{left:161px;top:2900px;width:878px;border:1px solid var(--line)}
.faq .q{height:44px;display:flex;align-items:center;justify-content:space-between;padding:0 14px;font-size:12px;text-transform:uppercase;color:#444;border-top:1px solid var(--line)}
.faq .q.active{background:var(--blue);color:#fff;height:38px;border-top:none}
.faq .a{padding:14px 34px 16px;font-size:12.5px;line-height:22px;color:var(--text)}
.plus{width:14px;height:14px;border-radius:50%;background:var(--blue);position:relative}
.plus::before,.plus::after{content:"";position:absolute;background:#fff;left:3px;top:6px;width:8px;height:2px}
.plus::after{left:6px;top:3px;width:2px;height:8px}
.q.active .plus{background:#fff}
.q.active .plus::before{background:var(--blue)}
.q.active .plus::after{display:none}

/* footer */
.footer{left:0;top:3250px;width:1200px;height:416px;background:var(--dark);color:var(--footer-text)}
.footer h5{position:absolute;top:99px;font-family:"Oswald",Arial,sans-serif;font-weight:500;color:#fff;font-size:16px;text-transform:uppercase;letter-spacing:.4px}
.contact-row{position:absolute;left:98px;display:flex;gap:20px;font-size:12.5px;line-height:20px;color:var(--footer-text)}
.links{position:absolute;top:143px;font-size:12.5px;line-height:34px}
.links div::before{content:"›";color:#fff;font-weight:700;margin-right:10px}
.input{position:absolute;left:829px;top:186px;width:270px;height:36px;border:1px solid #888;font-size:12px;color:#fff;padding:9px 10px}
.subscribe{position:absolute;left:829px;top:240px;width:110px;height:36px;border-radius:18px;background:var(--green);color:#fff;font-size:12px;font-weight:700;text-transform:uppercase;display:flex;align-items:center;justify-content:center}
.divider{position:absolute;left:98px;top:326px;width:1004px;height:1px;background:#444}
.copy{position:absolute;left:98px;top:359px;font-size:12px}
.social{position:absolute;left:1050px;top:344px;width:46px;height:46px;border-radius:50%;background:#1679b5}
</style>
</head>
<body>

<!-- header -->
<div class="abs topbar">
  <span>☎ +1-770-555-0143</span><span class="sep">|</span>
  <span>◷ Mon.-Fri: 9.00AM-5.00PM</span><span class="sep">|</span>
  <span>● PATIENT PORTAL</span>
</div>
<div class="abs logo">
  <div class="dot"></div>
  <div class="name">Maplecrest Behavioral Healthcare</div>
  <div class="tag">A Step Forwards Wellness</div>
</div>
<nav class="abs nav">
  <a style="left:412px">Home</a>
  <a style="left:494px">About Us</a>
  <a style="left:604px">Services</a>
  <a style="left:710px">Conditions We Treat</a>
  <a style="left:891px">New Patients</a>
  <a style="left:1025px">Contact Us</a>
</nav>

<!-- hero -->
<div class="abs hero" role="img" aria-label="Photo of a doctor in a white coat consulting a patient at a desk"></div>
<div class="abs hero-title">Maplecrest Behavioral Healthcare<br>A step forward in your wellness journey</div>
<div class="abs btn-outline">Take a Screening</div>
<div class="abs arrow" style="left:14px;top:440px"><svg width="12" height="12" viewBox="0 0 12 12"><path d="M8 1 3 6l5 5" fill="none" stroke="#fff" stroke-width="2"/></svg></div>
<div class="abs arrow" style="left:1148px;top:440px"><svg width="12" height="12" viewBox="0 0 12 12"><path d="M4 1l5 5-5 5" fill="none" stroke="#fff" stroke-width="2"/></svg></div>
<svg class="abs wave" style="top:690px" width="1200" height="100" viewBox="0 0 1200 100">
  <path d="M0 70 C300 30 700 0 1200 20 L1200 100 L0 100Z" fill="var(--green)"/>
  <path d="M0 82 C320 45 720 20 1200 40 L1200 100 L0 100Z" fill="#fff"/>
</svg>

<!-- services -->
<h2 class="abs heading" style="left:0;top:826px;width:1200px">Our Services</h2>
<p class="abs intro">We are Maplecrest Behavioral Healthcare, a mental health outpatient practice based in Georgia that sees diverse individuals and families from childhood to advanced age for a variety of conditions.</p>

<div class="abs service" style="left:108px">
  <div class="card"></div>
  <div class="icon"><svg width="44" height="40" viewBox="0 0 44 40" fill="none" stroke="#fff" stroke-width="2.5"><rect x="6" y="3" width="18" height="13" rx="1"/><path d="M9 10h4l2-4 2 7 2-3h3"/><path d="M3 36V20h38v16M3 28h38"/></svg></div>
  <div class="label">Diagnostic Evaluation<br>and Treatment</div>
</div>
<div class="abs service" style="left:362px">
  <div class="card"></div>
  <div class="icon"><svg width="44" height="40" viewBox="0 0 44 40" fill="none" stroke="#fff" stroke-width="2.5"><circle cx="18" cy="11" r="7"/><path d="M4 38c0-9 6-14 14-14s14 5 14 14"/><path d="M36 4v12M30 10h12"/></svg></div>
  <div class="label">Bariatric Pre-Surgical<br>Consultation</div>
</div>
<div class="abs service" style="left:611px">
  <div class="card"></div>
  <div class="icon"><svg width="44" height="40" viewBox="0 0 44 40" fill="none" stroke="#fff" stroke-width="2.5"><circle cx="18" cy="5" r="3"/><path d="M18 10v12h10l5 10"/><path d="M14 17a10 10 0 1 0 12 14"/></svg></div>
  <div class="label">Disability and Work<br>Related Reports</div>
</div>
<div class="abs service" style="left:863px">
  <div class="card"></div>
  <div class="icon"><svg width="44" height="40" viewBox="0 0 44 40" fill="none" stroke="#fff" stroke-width="2.5"><rect x="4" y="8" width="28" height="12" rx="6" transform="rotate(35 18 14)"/><circle cx="31" cy="28" r="8"/></svg></div>
  <div class="label">Early Childhood<br>Assessments</div>
</div>

<!-- about -->
<section class="abs about-panel">
  <h2>About Us</h2>
  <p style="top:134px">Nor again is there anyone who loves or pursues or desires to obtain pain of itself, because it is pain, but because occasionally circumstances occur.</p>
  <p style="top:200px">To take a trivial example, which of us ever undertakes laborious physical exercise, except to obtain some advantage from it? But who has any right to find fault with a man who chooses to enjoy a pleasure that has no annoying.</p>
</section>
<div class="abs btn-white">Read More ›</div>
<div class="abs about-photo" role="img" aria-label="Photo of a doctor and a nurse outdoors with a smiling senior patient in a wheelchair"></div>

<!-- blogs -->
<h2 class="abs heading" style="left:0;top:1778px;width:1200px">Latest Blogs &amp; News</h2>
<article class="abs post" style="left:98px">
  <div class="thumb" role="img" aria-label="Photo of a doctor consulting a patient" style="background:linear-gradient(135deg,#e9edf0,#b8c6d1 60%,#2a8fc4)"></div>
  <h3>Repeat Predefined Chunks</h3>
  <div class="meta"><i></i>by Owen <i></i>Sep 2017, <i></i>350</div>
  <p>Sed ut perspiciatis unde omnis iste natus error sit voluptatem accusantium doloremque</p>
</article>
<article class="abs post" style="left:420px">
  <div class="thumb" role="img" aria-label="Photo of a doctor reviewing a chart beside a hospital bed" style="background:linear-gradient(135deg,#d9cfc4,#8a6a5a 50%,#3c4c6a)"></div>
  <h3>Repeat Predefined Chunks</h3>
  <div class="meta"><i></i>by Owen <i></i>Sep 2017, <i></i>350</div>
  <p>Sed ut perspiciatis unde omnis iste natus error sit voluptatem accusantium doloremque</p>
</article>
<div class="abs news" style="top:1878px">
  <div class="thumb" role="img" aria-label="Photo of medical tools" style="background:linear-gradient(135deg,#f3a6b7,#d94c76)"></div>
  <h4>Lorem Ipsum is not in simply random text</h4>
  <div class="meta"><i></i>08 Apr 2017, &nbsp;Printing</div>
</div>
<div class="abs news" style="top:1990px">
  <div class="thumb" role="img" aria-label="Photo of a medical scan in progress" style="background:linear-gradient(135deg,#cfd8e0,#5b7f9d)"></div>
  <h4>Lorem Ipsum is not in simply random text</h4>
  <div class="meta"><i></i>08 Apr 2017, &nbsp;Printing</div>
</div>
<div class="abs news" style="top:2102px">
  <div class="thumb" role="img" aria-label="Photo of a surgical team in scrubs" style="background:linear-gradient(135deg,#d6eef2,#3fa6b5)"></div>
  <h4>Lorem Ipsum is not in simply random text</h4>
  <div class="meta"><i></i>08 Apr 2017, &nbsp;Printing</div>
</div>

<!-- testimonials -->
<section class="abs testimonials" role="img" aria-label="Background photo of a desk with a stethoscope, laptop and coffee cup">
  <h2 class="heading">What Our Patients Say</h2>
</section>
<div class="abs avatar" role="img" aria-label="Portrait of the reviewing patient"></div>
<div class="abs arrow" style="left:98px;top:2482px"><svg width="12" height="12" viewBox="0 0 12 12"><path d="M8 1 3 6l5 5" fill="none" stroke="#fff" stroke-width="2"/></svg></div>
<div class="abs arrow" style="left:1066px;top:2482px"><svg width="12" height="12" viewBox="0 0 12 12"><path d="M4 1l5 5-5 5" fill="none" stroke="#fff" stroke-width="2"/></svg></div>
<div class="abs qmark" style="left:230px;top:2532px">“</div>
<div class="abs qmark" style="left:870px;top:2590px">”</div>
<p class="abs quote">Lorem ipsum dolor sit amet, consectetur adipiscing elit, sed do eiusmod tempor incididunt ut labore et dolore magna aliqua. Ut enim ad minim veniam, quis nostrud exercitation ullamco laboris nisi ut</p>
<div class="abs author">NADIA BROOKS , <span>Creative Manager.</span></div>

<!-- faq -->
<h2 class="abs heading" style="left:0;top:2810px;width:1200px">FAQ</h2>
<div class="abs faq">
  <div class="q active"><span>Q1: How do you know if you need to see a psychiatrist, therapist, counselor or psychotherapist?</span><span class="plus"></span></div>
  <div class="a">If you're interested or curious, just go. People go to therapy for a host of reasons – anything from getting support, to getting help for major mental illness, to working through a particular issue(s), to just getting an outsider's perspective</div>
  <div class="q"><span>Q2: Why is my child not doing well in school?</span><span class="plus"></span></div>
  <div class="q"><span>Q3: I feel sad, tired and I do not have energy. Is that normal?</span><span class="plus"></span></div>
  <div class="q"><span>Q4: I am have trouble with my child. Do you do therapy for children?</span><span class="plus"></span></div>
</div>

<!-- footer -->
<svg class="abs wave" style="top:3180px" width="1200" height="90" viewBox="0 0 1200 90">
  <path d="M0 70 C400 75 800 40 1200 0 L1200 90 L0 90Z" fill="var(--green)"/>
  <path d="M0 80 C400 85 800 55 1200 18 L1200 90 L0 90Z" fill="var(--dark)"/>
</svg>
<footer class="abs footer">
  <h5 style="left:98px">Contact Us</h5>
  <div class="contact-row" style="top:140px"><svg width="16" height="18" viewBox="0 0 16 18" fill="none" stroke="#ccc" stroke-width="1.5"><path d="M8 17s6-6 6-10A6 6 0 0 0 2 7c0 4 6 10 6 10z"/><circle cx="8" cy="7" r="2"/></svg><span>214 Birchwood Lane,<br>Fayetteville, GA</span></div>
  <div class="contact-row" style="top:204px"><svg width="16" height="16" viewBox="0 0 16 16" fill="none" stroke="#ccc" stroke-width="1.5"><path d="M3 1h3l1 4-2 1a9 9 0 0 0 5 5l1-2 4 1v3c0 1-1 2-2 2C7 15 1 9 1 3c0-1 1-2 2-2z"/></svg><span>(+1) 770 555 0198</span></div>
  <div class="contact-row" style="top:246px"><svg width="16" height="14" viewBox="0 0 16 14" fill="none" stroke="#ccc" stroke-width="1.5"><rect x="1" y="1" width="14" height="12"/><path d="M1 1l7 6 7-6"/></svg><span>hello@maplecrestbh.com</span></div>

  <h5 style="left:398px">Quick Links</h5>
  <div class="links" style="left:404px"><div>Home</div><div>About Us</div><div>Patient Portal</div><div>Services</div></div>
  <div class="links" style="left:590px"><div>Contact us</div><div>Book A Callback</div><div>FAQs</div><div>Terms &amp; Conditions</div></div>

  <h5 style="left:829px">Newsletter Subscription</h5>
  <p style="position:absolute;left:829px;top:136px;width:290px;font-size:12.5px;line-height:20px">Register your Email Address to get information about us and services</p>
  <div class="input">Email Address</div>
  <div class="subscribe">Subscribe</div>

  <div class="divider"></div>
  <div class="copy">© Copyright 2017 Maplecrest Behavioral Healthcare. All Rights Reserved</div>
  <div class="social" aria-label="Social profile link"></div>
</footer>

</body>
</html>
```